TA BRAMLEY BUSINESS CARD DESIGN PROJECT

We need to utilize our logo that was expertly created on PixelHarbor and now need to match this with a business card design.

```html
<!DOCTYPE html>
<html lang="en">
<head>
<meta charset="utf-8">
<title>TA Bramley Business Card</title>
<link href="https://fonts.googleapis.com/css2?family=Open+Sans:wght@400;600;700&display=swap" rel="stylesheet">
<style>
  :root {
    --backdrop: #3b3b3b;
    --card: #161616;
    --card-edge: #1c5ec8;
    --brand-blue: #1a5bbf;
    --text-light: #e6e6e6;
    --divider: #2c4f86;
    --pattern-dark: #1c1c1c;
    --pattern-light: #2e2e2e;
  }
  * { margin: 0; padding: 0; box-sizing: border-box; }
  html, body {
    width: 1200px; height: 801px; overflow: hidden;
    background: var(--backdrop);
    font-family: "Open Sans", Arial, sans-serif;
  }
  .stage {
    position: relative; width: 1200px; height: 801px;
    display: flex; align-items: center; justify-content: center; gap: 60px;
  }
  .card {
    position: relative; width: 500px; height: 286px;
    background: var(--card);
    border-bottom: 3px solid var(--card-edge);
    border-left: 2px solid var(--card-edge);
    box-shadow: 0 14px 30px rgba(0,0,0,0.45);
    overflow: hidden;
  }
  /* front */
  .brand-block {
    position: absolute; left: 44px; top: 70px; width: 230px;
  }
  .brand-name {
    color: var(--brand-blue); font-weight: 700;
    font-size: 38px; line-height: 1.05; letter-spacing: 3px;
  }
  .holder { position: absolute; left: 44px; top: 196px; }
  .holder-name {
    color: var(--brand-blue); font-weight: 600;
    font-size: 19px; letter-spacing: 1px;
  }
  .holder-title { color: var(--text-light); font-size: 14px; margin-top: 2px; }
  .divider {
    position: absolute; left: 292px; top: 98px;
    width: 1px; height: 92px; background: var(--divider);
  }
  .contact-list {
    position: absolute; left: 312px; top: 100px; list-style: none;
  }
  .contact-list li {
    display: flex; align-items: center; gap: 8px;
    color: var(--text-light); font-size: 13px; line-height: 28px;
  }
  .contact-list svg { width: 12px; height: 12px; fill: var(--brand-blue); flex: none; }
  /* back */
  .pattern-field {
    position: absolute; inset: 0;
    background: linear-gradient(135deg, var(--pattern-dark) 0%, var(--pattern-light) 100%);
  }
  .back-brand {
    position: absolute; left: 0; right: 0; top: 128px; text-align: center;
    color: var(--brand-blue); font-weight: 700; font-size: 22px; letter-spacing: 2px;
  }
</style>
</head>
<body>
<main class="stage">
  <section class="card card-front" aria-label="Business card front">
    <div class="brand-block">
      <div class="brand-name">TA<br>BRAMLEY</div>
    </div>
    <div class="holder">
      <div class="holder-name">DANA RIVERTON</div>
      <div class="holder-title">President</div>
    </div>
    <div class="divider"></div>
    <ul class="contact-list">
      <li>
        <svg viewBox="0 0 24 24" aria-hidden="true"><path d="M6.6 10.8a15.5 15.5 0 0 0 6.6 6.6l2.2-2.2a1 1 0 0 1 1-.25 11.4 11.4 0 0 0 3.6.57 1 1 0 0 1 1 1V20a1 1 0 0 1-1 1A17 17 0 0 1 3 4a1 1 0 0 1 1-1h3.5a1 1 0 0 1 1 1c0 1.25.2 2.45.57 3.57a1 1 0 0 1-.25 1z"/></svg>
        555-310-4827
      </li>
      <li>
        <svg viewBox="0 0 24 24" aria-hidden="true"><path d="M2 5h20v14H2zm2 2v.5l8 5 8-5V7l-8 5z"/></svg>
        d.riverton@tabramley.com
      </li>
      <li>
        <svg viewBox="0 0 24 24" aria-hidden="true"><circle cx="12" cy="12" r="10"/></svg>
        www.tabramley.com
      </li>
    </ul>
  </section>

  <section class="card card-back" aria-label="Business card back">
    <div class="pattern-field" role="img" aria-label="Repeating tone-on-tone brand pattern across the card back"></div>
    <div class="back-brand">TA BRAMLEY</div>
  </section>
</main>
</body>
</html>
```